Meridale Bed Company Needs Business Card

Looking for a very nice looking business card. Creative but not extravagant. We sell beds and pillows across the U.S. and need something professional but catchy. I have attached the logo.

Name : Devin Holt
Title : President
Phone : (800) 471-2960
Email: sleep@quilmora.com
Website: www.quilmora.com

Can be single-sided or double-sided
horizontal or vertical

Can use Blues/Greys

Target Market(s)

Mass Market

Industry/Entity Type

Retail

Contact Information for Business Card

Name : Devin Holt
Title : President
Phone : (800) 471-2960
Email: sleep@quilmora.com
Website: www.quilmora.com

Requirements
Must have
• Clean, Modern, Smooth
• Can use Blues/Greys
• On the other side without the information - have something simple like www.quilmora.com or our logo
Nice to have
• Surprise me
Should not have
• Nothing crazy, nothing cluttered

```html
<!DOCTYPE html>
<html lang="en">
<head>
<meta charset="utf-8">
<title>Meridale Bed Company – Business Card</title>
<link rel="stylesheet" href="https://fonts.googleapis.com/css2?family=Source+Sans+3:wght@400;600&display=swap">
<style>
  :root {
    --backdrop: #6a6a6a;
    --card-light: #ffffff;
    --card-dark: #141414;
    --ink-dark: #1a1a1a;
    --ink-light: #ffffff;
  }
  * { margin: 0; padding: 0; box-sizing: border-box; }
  html, body {
    width: 1200px;
    height: 900px;
    overflow: hidden;
  }
  body {
    background: var(--backdrop);
    font-family: "Source Sans 3", Arial, sans-serif;
    position: relative;
  }
  .card {
    position: absolute;
    left: 381px;
    width: 439px;
    height: 270px;
    border-radius: 12px;
    text-align: center;
  }
  .card--front {
    top: 161px;
    background: var(--card-light);
    color: var(--ink-dark);
  }
  .card--back {
    top: 497px;
    background: var(--card-dark);
    color: var(--ink-light);
  }
  .wordmark {
    position: absolute;
    left: 0;
    right: 0;
    font-size: 50px;
    font-weight: 400;
    letter-spacing: 1px;
    line-height: 1;
  }
  .card--front .wordmark { top: 58px; }
  .card--back .wordmark { top: 112px; }
  .contact {
    position: absolute;
    top: 130px;
    left: 0;
    right: 0;
    line-height: 1.2;
  }
  .contact__name {
    font-size: 16px;
    font-weight: 600;
  }
  .contact__title {
    font-size: 14px;
    margin-bottom: 13px;
  }
  .contact__line {
    font-size: 14px;
  }
  .web-address {
    position: absolute;
    top: 216px;
    left: 0;
    right: 0;
    font-size: 13px;
    font-weight: 600;
  }
</style>
</head>
<body>
  <section class="card card--front">
    <div class="wordmark">quilmora</div>
    <div class="contact">
      <p class="contact__name">Devin Holt</p>
      <p class="contact__title">President</p>
      <p class="contact__line">(800) 471-2960</p>
      <p class="contact__line">sleep@quilmora.com</p>
    </div>
  </section>
  <section class="card card--back">
    <div class="wordmark">quilmora</div>
    <p class="web-address">www.quilmora.com</p>
  </section>
</body>
</html>
```